Animal Eye Clinic needs a Business card

We are a new veterinary ophthalmology practice (Ridgeline Pet Vision Care) and we need a business card designed. We only see animal eyes - we are not a regular veterinary clinic. We already have a logo. We are looking for a professional, good looking business card to hand out to our clients. We are looking for something simple but professional and contemporary. Our logo is likely the only picture/graphic that needs to be on the card.
Updates

Contact Information for Business Card

Delia Vossman, BSc, DVM, MSc, DipACVO
Veterinary Ophthalmologist

Phone: 250.418.3927
Email: ridgelinepetvisioncare@mailbox-example.net
Website: ridgelinepetvisioncare-example.net
Address: 1874 Thornbury Rd
Kelowna, BC, V1X 4M9

Colors

Designer to choose colors to be used in the design.

Requirements
Must have
• Our logo (attached)

```html
<!DOCTYPE html>
<html lang="en">
<head>
<meta charset="UTF-8">
<title>Ridgeline Pet Vision Care – Business Card</title>
<link rel="stylesheet" href="https://fonts.googleapis.com/css2?family=Roboto:wght@400;500;700&display=swap">
<style>
  :root {
    --teal: #1a7f7b;
    --teal-light: #4fa29e;
    --slate: #5e5f61;
    --text-grey: #4d4f52;
    --card: #f4f2ee;
    --card-edge: #e2ded7;
    --backdrop: #d9d4cc;
  }
  * { box-sizing: border-box; margin: 0; padding: 0; }
  html, body {
    width: 1200px;
    height: 1200px;
    overflow: hidden;
    background: var(--backdrop);
    font-family: "Roboto", Arial, sans-serif;
  }
  .business-card {
    position: absolute;
    left: 80px;
    top: 303px;
    width: 1040px;
    height: 594px;
    background: var(--card);
    border: 1px solid var(--card-edge);
    border-radius: 18px;
    overflow: hidden;
    box-shadow: 0 10px 30px rgba(0,0,0,0.10);
  }
  .brand {
    position: absolute;
    left: 50px;
    top: 62px;
    display: flex;
    align-items: center;
    gap: 16px;
  }
  .brand-dot {
    width: 54px;
    height: 54px;
    border-radius: 50%;
    background: var(--teal);
  }
  .brand-name {
    font-weight: 700;
    font-size: 30px;
    color: var(--teal);
    letter-spacing: 0.3px;
  }
  .person {
    position: absolute;
    left: 50px;
    top: 172px;
  }
  .person-marker {
    position: absolute;
    left: -43px;
    top: 9px;
    width: 0;
    height: 0;
    border-top: 12px solid transparent;
    border-bottom: 12px solid transparent;
    border-left: 18px solid var(--teal);
  }
  .person-name {
    font-weight: 700;
    font-size: 33px;
    color: var(--teal);
    letter-spacing: 0.5px;
    line-height: 1.2;
  }
  .person-credentials {
    font-size: 23px;
    color: var(--teal);
    margin-top: 4px;
  }
  .person-title {
    font-size: 23px;
    color: var(--text-grey);
    margin-top: 8px;
  }
  .address {
    position: absolute;
    left: 50px;
    top: 330px;
    font-size: 23px;
    color: var(--text-grey);
    line-height: 39px;
  }
  .contact-list {
    position: absolute;
    left: 50px;
    top: 418px;
    list-style: none;
    font-size: 21px;
    color: var(--text-grey);
  }
  .contact-list li {
    display: flex;
    align-items: center;
    gap: 6px;
    height: 36px;
  }
  .contact-list svg { width: 18px; height: 18px; flex: none; }
  .phone-number { font-size: 23px; }
  .mascot-area {
    position: absolute;
    right: 0;
    top: 0;
    width: 450px;
    height: 594px;
    background: linear-gradient(160deg, var(--teal) 0%, var(--teal-light) 55%, var(--slate) 100%);
    border-top-left-radius: 220px;
    border-bottom-left-radius: 120px;
    opacity: 0.92;
  }
</style>
</head>
<body>
  <section class="business-card">
    <header class="brand">
      <span class="brand-dot"></span>
      <span class="brand-name">Ridgeline Pet Vision Care</span>
    </header>

    <div class="person">
      <span class="person-marker"></span>
      <h1 class="person-name">DELIA VOSSMAN</h1>
      <p class="person-credentials">BSc, DVM, MSc, DipACVO</p>
      <p class="person-title">Veterinary Ophthalmologist</p>
    </div>

    <address class="address" style="font-style: normal;">
      1874 Thornbury Rd<br>
      Kelowna, BC, V1X 4M9
    </address>

    <ul class="contact-list">
      <li>
        <svg viewBox="0 0 24 24" aria-hidden="true"><path fill="#1a7f7b" d="M6.6 10.8a15.1 15.1 0 0 0 6.6 6.6l2.2-2.2a1 1 0 0 1 1-.25 11.4 11.4 0 0 0 3.6.57 1 1 0 0 1 1 1V20a1 1 0 0 1-1 1A17 17 0 0 1 3 4a1 1 0 0 1 1-1h3.5a1 1 0 0 1 1 1c0 1.25.2 2.45.57 3.57a1 1 0 0 1-.25 1z"/></svg>
        <span class="phone-number">250.418.3927</span>
      </li>
      <li>
        <svg viewBox="0 0 24 24" aria-hidden="true"><rect x="2" y="5" width="20" height="14" rx="2" fill="#1a7f7b"/><path d="M3 6.5l9 6 9-6" stroke="#f4f2ee" stroke-width="1.8" fill="none"/></svg>
        <span>ridgelinepetvisioncare@mailbox-example.net</span>
      </li>
      <li>
        <svg viewBox="0 0 24 24" aria-hidden="true"><circle cx="12" cy="12" r="10" fill="#1a7f7b"/><path d="M2 12h20M12 2c3 3 3 17 0 20M12 2c-3 3-3 17 0 20" stroke="#f4f2ee" stroke-width="1.5" fill="none"/></svg>
        <span>ridgelinepetvisioncare-example.net</span>
      </li>
    </ul>

    <div class="mascot-area" role="img" aria-label="Large illustration of a horse, dog and cat silhouette in teal and grey"></div>
  </section>
</body>
</html>
```